Human Resource Consulting practice needs a business card design

We need a business card design (double sided colour) for our Human Resource (HR) consulting practice in regional New South Wales, australia. Our business name is Staff Compass. We support small and medium business across the Mid North Coast of New South Wales by providing them with outsourced HR support, services and products to help them achieve compliance with workplace legislation and across all areas of the employment lifecycle from recruitment to termination and everything in between. Our corporate colours are hot pink and black. The final design should communicate professionalism, trust, people focus.
I have attached the current (old) business card for your reference.

Target Market(s)

Business owners and high level managers

Industry/Entity Type

Business

Contact Information for Business Card

Name
Title
Phone no
Mobile no
Address
PO Box
email address
website

Colors
e34197

Requirements
Must have
• Tempate for changing business card personal details including Name, position title, mobile number, email address.
• Keep current logo and colours as per attached
• Logo must be presented in 2 colours or black only not white
Nice to have
• One side logo and graphic only other side logo and personal details
Should not have
• Should not be the same as the current version (attached) but a modern interpretation.
• Does not need a busy reverse side with our list of services as per current version. I feel this is too busy.
• No photos

```html
<!DOCTYPE html>
<html lang="en">
<head>
<meta charset="utf-8">
<title>Staff Compass – Business Card</title>
<link rel="stylesheet" href="https://fonts.googleapis.com/css2?family=Arimo:wght@400;700&family=Michroma&display=swap">
<style>
  :root {
    --pink: #e34197;
    --ink: #1c1c1e;
    --stage: #2b2b2d;
    --card-dark: #242426;
    --card-light: #f4f4f5;
    --facet-a: #ffffff;
    --facet-b: #e4e4e6;
    --facet-c: #d3d3d6;
    --muted: #3a3a3c;
  }
  * { box-sizing: border-box; margin: 0; padding: 0; }
  html, body {
    width: 1200px; height: 873px; overflow: hidden;
    background: var(--stage);
  }
  .stage {
    position: relative; width: 1200px; height: 873px;
  }
  .card {
    position: absolute; top: 271px;
    width: 540px; height: 330px;
    border-radius: 18px; overflow: hidden;
    box-shadow: 0 10px 30px rgba(0,0,0,.45);
  }
  .card--back { left: 40px; background: var(--card-dark); }
  .card--front { left: 620px; background: var(--card-light); }

  .brand {
    position: absolute;
    display: flex; align-items: center; gap: 8px;
    font-family: "Arimo", Arial, sans-serif;
    font-weight: 700; color: var(--pink);
    white-space: nowrap;
  }
  .brand__dot {
    width: 8px; height: 8px; border-radius: 50%;
    background: var(--pink);
  }
  .card--back .brand { left: 50%; top: 46%; transform: translate(-50%, -50%); font-size: 40px; }
  .card--front .brand { left: 130px; top: 40px; font-size: 32px; }

  .facets {
    position: absolute; inset: 0;
    background:
      linear-gradient(125deg, transparent 0 30%, rgba(210,210,214,.35) 30% 46%, transparent 46%),
      linear-gradient(40deg, var(--facet-b) 0%, var(--facet-a) 35%, var(--facet-c) 60%, var(--facet-a) 85%, var(--facet-b) 100%);
  }

  .divider {
    position: absolute; left: 290px; top: 95px;
    width: 2px; height: 125px;
    background: linear-gradient(to bottom, transparent, var(--pink) 25%, var(--pink) 75%, transparent);
  }
  .person {
    position: absolute; right: 262px; top: 138px;
    text-align: right; font-family: "Arimo", Arial, sans-serif;
  }
  .person__name { color: var(--pink); font-weight: 700; font-size: 17px; }
  .person__title { color: var(--ink); font-size: 13px; margin-top: 3px; }

  .contacts {
    position: absolute; left: 308px; top: 98px;
    list-style: none; font-family: "Michroma", sans-serif;
    font-size: 10.5px; color: var(--ink); line-height: 21px;
  }
  .contacts__label { color: var(--pink); display: inline-block; width: 26px; font-weight: 700; }
  .contacts__email { font-size: 9px; }
  .contacts__web { color: var(--pink); font-size: 10px; }

  .address {
    position: absolute; left: 130px; bottom: 36px;
    font-family: "Michroma", sans-serif; font-size: 12.5px;
    color: var(--pink); letter-spacing: .3px;
  }
</style>
</head>
<body>
<main class="stage">
  <section class="card card--back" aria-label="Card reverse">
    <div class="brand"><span>Staff Compass</span><span class="brand__dot"></span></div>
  </section>

  <section class="card card--front" aria-label="Card front">
    <div class="facets" role="img" aria-label="Faceted low-poly background in pale silver greys"></div>
    <div class="brand"><span>Staff Compass</span><span class="brand__dot"></span></div>
    <div class="divider"></div>
    <div class="person">
      <p class="person__name">Maria Kellan</p>
      <p class="person__title">Principal Consultant</p>
    </div>
    <ul class="contacts">
      <li><span class="contacts__label">T:</span>02 5550 1482</li>
      <li><span class="contacts__label">M:</span>0400 555 318</li>
      <li><span class="contacts__label">F:</span>02 5550 1483</li>
      <li><span class="contacts__label">E:</span><span class="contacts__email">maria@staffcompass.com.au</span></li>
      <li><span class="contacts__label"></span><span class="contacts__web">www.staffcompass.com.au</span></li>
    </ul>
    <p class="address">PO Box 218, Kestrel Bay, NSW 2400</p>
  </section>
</main>
</body>
</html>
```